Enterprise image desing

The designs are for a fashion store for young men and women.
Updates

Los diseƱos parecen similares

Target Market(s)

Young

Font styles to use
Sans Serif

Colors
ec1f27
ffffff
1b1b1b

Requirements
Must have
• Use clean and modern sources
Nice to have
• n / a
Should not have
• n / a

```html
<!DOCTYPE html>
<html lang="en">
<head>
<meta charset="utf-8">
<title>Velmora — Stationery Set</title>
<link href="https://fonts.googleapis.com/css2?family=Work+Sans:wght@400;500;700&display=swap" rel="stylesheet">
<style>
:root{
  --navy:#08284a;
  --red:#ec1f27;
  --white:#ffffff;
  --ink:#1b1b1b;
  --grey-text:#8a8a8a;
  --bg:#b0b0b0;
  --flap:#d9d9d9;
}
*{margin:0;padding:0;box-sizing:border-box}
html,body{width:1037px;height:1200px;overflow:hidden}
body{background:var(--bg);font-family:"Work Sans",sans-serif;position:relative;color:var(--ink)}
.piece{position:absolute;overflow:hidden}
.brand{display:flex;align-items:center;gap:6px;font-family:"Work Sans",sans-serif;font-weight:700;color:var(--navy);letter-spacing:.5px;white-space:nowrap}
.brand .mark{background:var(--red);display:block}
.brand--light{color:var(--white)}
.corner{position:absolute;right:0;bottom:0;background:var(--red);border-top-left-radius:10px}
.footer-band{position:absolute;left:0;right:0;bottom:0;background:var(--navy);color:var(--white);display:flex;align-items:center}
.contacts{list-style:none;font-size:6px;line-height:1.35}
.contacts li{display:flex;align-items:center;gap:3px}
.contacts svg{width:5px;height:5px;fill:var(--white)}
.address{font-size:6px;line-height:1.35}

/* letterhead */
.letter-back{left:141px;top:104px;width:357px;height:486px;background:var(--navy)}
.letterhead{left:86px;top:59px;width:358px;height:487px;background:var(--white)}
.letterhead .brand{position:absolute;left:26px;top:22px;font-size:19px}
.letterhead .brand .mark{width:18px;height:18px}
.salutation{position:absolute;left:26px;top:120px;font-size:10px;color:var(--grey-text)}
.body-copy{position:absolute;left:26px;top:152px;width:310px;font-size:6.3px;line-height:1.5;color:var(--grey-text)}
.body-copy p{margin-bottom:8px}
.signature{position:absolute;left:26px;top:367px;width:100px;height:24px;background:linear-gradient(90deg,#e6e6e6,#f4f4f4)}
.letterhead .footer-band{height:46px;padding-left:26px;gap:18px}
.letterhead .corner{width:48px;height:46px}

/* business cards */
.card-front{left:569px;top:81px;width:198px;height:113px;background:var(--white)}
.card-front .brand{position:absolute;left:10px;top:12px;font-size:11px;gap:4px}
.card-front .brand .mark{width:11px;height:11px}
.card-name{position:absolute;left:10px;top:54px;font-size:6px;font-weight:500;color:var(--red)}
.card-role{position:absolute;left:10px;top:62px;font-size:4.5px;color:var(--ink)}
.card-front .address{position:absolute;right:10px;top:55px;text-align:right;font-size:4.5px;color:var(--ink)}
.card-front .footer-band{height:39px;padding-left:10px}
.card-front .contacts{font-size:4.5px}
.card-front .contacts svg{width:4px;height:4px}
.card-front .corner{width:42px;height:39px}
.card-back{left:779px;top:81px;width:198px;height:113px;background:var(--navy);display:flex;align-items:center;justify-content:center}
.card-back .brand{font-size:17px}
.card-back .brand .mark{width:16px;height:16px}

/* envelope back (sits behind the front envelope) */
.envelope-back{left:626px;top:346px;width:351px;height:248px;background:var(--navy);z-index:1}
.envelope-back .flap{position:absolute;left:0;top:0;width:351px;height:120px}
.envelope-back .brand{position:absolute;left:0;right:0;top:178px;justify-content:center;font-size:16px}
.envelope-back .brand .mark{width:15px;height:15px}

/* envelope front */
.envelope{left:529px;top:226px;width:353px;height:166px;background:var(--white);z-index:2}
.envelope .brand{position:absolute;left:16px;top:8px;font-size:16px}
.envelope .brand .mark{width:15px;height:15px}
.envelope .footer-band{height:44px;padding-left:16px;gap:18px}
.envelope .corner{width:48px;height:44px}

/* folder */
.folder-cover{left:213px;top:686px;width:310px;height:460px;background:var(--navy)}
.folder-cover .brand{position:absolute;left:21px;bottom:24px;font-size:21px}
.folder-cover .brand .mark{width:20px;height:20px}
.folder-inside{left:523px;top:686px;width:310px;height:460px;background:linear-gradient(90deg,#ececec,#ffffff 70%)}
.folder-inside .brand{position:absolute;left:18px;top:42px;font-size:16px}
.folder-inside .brand .mark{width:15px;height:15px}
.folder-inside .footer-band{height:40px;padding-left:12px;gap:16px}
.folder-inside .corner{width:40px;height:40px}
</style>
</head>
<body>
<svg width="0" height="0" style="position:absolute" aria-hidden="true">
  <symbol id="i-phone" viewBox="0 0 10 10"><path d="M2 0h2l1 3-1.5 1a6 6 0 0 0 2.5 2.5L7 5l3 1v2a2 2 0 0 1-2 2A8 8 0 0 1 0 2a2 2 0 0 1 2-2z"/></symbol>
  <symbol id="i-mobile" viewBox="0 0 10 10"><rect x="2.5" y="0" width="5" height="10" rx="1"/></symbol>
  <symbol id="i-mail" viewBox="0 0 10 10"><path d="M0 2h10v6H0zM0 2l5 3 5-3" /></symbol>
  <symbol id="i-web" viewBox="0 0 10 10"><circle cx="5" cy="5" r="5"/></symbol>
</svg>

<!-- letterhead -->
<div class="piece letter-back"></div>
<section class="piece letterhead">
  <div class="brand"><span class="mark"></span>VELMORA</div>
  <p class="salutation">Dear sir,</p>
  <div class="body-copy">
    <p>Lorem ipsum dolor sit amet, an vel recteque dissentiet, detracto albucius platonem ex vel, eros repudiandae cu. Atqui aliquando nec an, unum graece adolescens vel ad. Id odio scae has, iudico euismod atomorum ius ea, cum ea honestatis quaerendum theophrastus. Mea honestatis quaerendum theophrastus. Mea</p>
    <p>Lorem ipsum dolor sit amet, an vel recteque dissentiet, detracto albucius platonem ex vel, eros repudiandae cu. Atqui aliquando nec an, unum graece adolescens vel ad. Id odio scae has, iudico euismod atomorum ius ea, cum ea honestatis quaerendum theophrastus. Mea doming repudiandae ex, cu cum civibus assentior posidonium. Quo etiam pertinax ex, te eros repudiandae cu. Atqui aliquando nec an, unum graece adolescens vel ad. Id odio scae honestatis quaerendum theophrastus. Mea</p>
    <p>Lorem ipsum dolor sit amet, an vel recteque dissentiet, detracto albucius platonem ex vel, eros repudiandae cu. Atqui aliquando nec an, unum graece adolescens vel ad. Id odio scae has, iudico euismod atomorum ius ea, cum ea honestatis quaerendum theophrastus. Mea honestatis quaerendum theophrastus. Mea</p>
    <p>eros repudiandae cu. Atqui aliquando nec an, unum graece adolescens vel ad. Id odio scae honestatis quaerendum theophrastus. Mea posidonium. Quo etiam pertinax ex, te etiam pertinax ex, te</p>
  </div>
  <div class="signature" role="img" aria-label="Handwritten signature"></div>
  <footer class="footer-band">
    <ul class="contacts">
      <li><svg><use href="#i-phone"/></svg>+593 7 210-4480</li>
      <li><svg><use href="#i-mobile"/></svg>+593 98 310-7721</li>
      <li><svg><use href="#i-mail"/></svg>apino@velmora.com</li>
      <li><svg><use href="#i-web"/></svg>www.velmora.com</li>
    </ul>
    <p class="address">Calle Olmedo y Sucre,<br>Ecuador, EC070115</p>
    <span class="corner"></span>
  </footer>
</section>

<!-- business cards -->
<section class="piece card-front">
  <div class="brand"><span class="mark"></span>VELMORA</div>
  <p class="card-name">ANDRÉS PINO VERA</p>
  <p class="card-role">Gerente General</p>
  <p class="address">Calle Olmedo y Sucre,<br>Ecuador, EC070115</p>
  <footer class="footer-band">
    <ul class="contacts">
      <li><svg><use href="#i-phone"/></svg>+593 7 210-4480</li>
      <li><svg><use href="#i-mobile"/></svg>+593 98 310-7721</li>
      <li><svg><use href="#i-mail"/></svg>apino@velmora.com</li>
      <li><svg><use href="#i-web"/></svg>www.velmora.com</li>
    </ul>
    <span class="corner"></span>
  </footer>
</section>
<section class="piece card-back">
  <div class="brand brand--light"><span class="mark"></span>VELMORA</div>
</section>

<!-- envelope back -->
<section class="piece envelope-back">
  <svg class="flap" viewBox="0 0 351 120" preserveAspectRatio="none" aria-hidden="true">
    <polygon points="0,0 351,0 330,120 21,120" fill="var(--flap)"/>
  </svg>
  <div class="brand brand--light"><span class="mark"></span>VELMORA</div>
</section>

<!-- envelope front -->
<section class="piece envelope">
  <div class="brand"><span class="mark"></span>VELMORA</div>
  <footer class="footer-band">
    <ul class="contacts">
      <li><svg><use href="#i-phone"/></svg>+593 7 210-4480</li>
      <li><svg><use href="#i-mobile"/></svg>+593 98 310-7721</li>
      <li><svg><use href="#i-mail"/></svg>apino@velmora.com</li>
      <li><svg><use href="#i-web"/></svg>www.velmora.com</li>
    </ul>
    <p class="address">Calle Olmedo y Sucre,<br>Ecuador, EC070115</p>
    <span class="corner"></span>
  </footer>
</section>

<!-- presentation folder -->
<section class="piece folder-cover">
  <div class="brand brand--light"><span class="mark"></span>VELMORA</div>
</section>
<section class="piece folder-inside">
  <div class="brand"><span class="mark"></span>VELMORA</div>
  <footer class="footer-band">
    <ul class="contacts">
      <li><svg><use href="#i-phone"/></svg>+593 7 210-4480</li>
      <li><svg><use href="#i-mobile"/></svg>+593 98 310-7721</li>
      <li><svg><use href="#i-mail"/></svg>apino@velmora.com</li>
      <li><svg><use href="#i-web"/></svg>www.velmora.com</li>
    </ul>
    <p class="address">Calle Olmedo y Sucre,<br>Ecuador, EC070115</p>
    <span class="corner"></span>
  </footer>
</section>
</body>
</html>
```